Business Card Design

I am an Event and Wedding Planner in need of an eye catching business card featuring my logo (attached), my contact details, and my company tagline (Making every celebration glow with wonder...) I would like the tagline in font similar the logo's font.
Updates
I have just noticed that my logo has a misspelling so for the final design, I will be uploading a corrected logo as soon as I have it.
My apologies.
Reason: Waiting on a corrected logo...Lantern is misspelled and it should say Weddings not Wedding
The logo has been corrected so now Lantern is spelled correctly and it says Weddings instead of Wedding. Please use Edwardian Script ITC as the font for the tagline so it will match the logo. Thank you for your patience.
Target Market(s)
Engaged couples and people hosting milestone celebrations. 25-50 years old, predominately female
Industry/Entity Type
Business
Contact Information for Business Card
Rosalind Merrow, Event Manager / Owner, Mobile: 0491 868 254, Email: rosalind@velvetlanternco.com.au, www.velvetlanternco.com.au, Making every celebration glow with wonder...

```html
<!DOCTYPE html>
<html lang="en">
<head>
<meta charset="utf-8">
<title>Velvet Lantern – Business Card</title>
<link href="https://fonts.googleapis.com/css2?family=Oswald:wght@500&family=Raleway:wght@400;500&family=Pinyon+Script&display=swap" rel="stylesheet">
<style>
  :root {
    --bg: #d6d6d6;
    --card: #ffffff;
    --ink: #111111;
    --muted: #555555;
    --rule: #9a9a9a;
    --accent: #c0392b;
  }
  * { box-sizing: border-box; margin: 0; padding: 0; }
  html, body { width: 1200px; height: 947px; overflow: hidden; }
  body {
    background: var(--bg);
    font-family: "Raleway", sans-serif;
    color: var(--ink);
    position: relative;
  }
  .card {
    position: absolute;
    left: 280px;
    width: 640px;
    height: 366px;
    background: var(--card);
    border-radius: 24px;
    box-shadow: 0 4px 14px rgba(0,0,0,0.12);
  }
  .card--back { top: 70px; }
  .card--front { top: 500px; }

  /* back */
  .social {
    position: absolute;
    right: 34px;
    bottom: 28px;
    display: flex;
    gap: 18px;
    font-size: 11px;
    color: var(--muted);
  }
  .social__item { display: flex; align-items: center; gap: 6px; }
  .social__mark { width: 16px; height: 16px; background: var(--ink); }

  /* front */
  .brand {
    position: absolute;
    left: 40px;
    top: 28px;
    width: 300px;
  }
  .brand__name {
    display: flex;
    align-items: center;
    gap: 10px;
    font-size: 34px;
    font-weight: 400;
    line-height: 1.1;
  }
  .brand__dot { width: 12px; height: 12px; border-radius: 50%; background: var(--accent); flex: none; }
  .brand__rule { height: 1px; background: var(--rule); margin: 8px 0 6px; }
  .brand__sub { font-size: 16px; letter-spacing: 0.5px; }
  .brand__tagline {
    font-family: "Pinyon Script", cursive;
    font-size: 22px;
    line-height: 1.2;
    margin-top: 4px;
    white-space: nowrap;
  }

  .contact {
    position: absolute;
    left: 60px;
    top: 150px;
    display: flex;
    flex-direction: column;
    gap: 18px;
  }
  .contact__row { display: flex; align-items: center; gap: 12px; }
  .contact__icon { width: 34px; height: 34px; flex: none; }
  .contact__bar { width: 4px; height: 40px; background: var(--rule); flex: none; }
  .contact__bar--tall { height: 58px; }
  .contact__text { font-size: 15px; line-height: 1.35; letter-spacing: 0.6px; }
  .person__name {
    font-family: "Oswald", sans-serif;
    font-weight: 500;
    font-size: 24px;
    letter-spacing: 1px;
    text-transform: uppercase;
    line-height: 1;
  }
  .person__role { font-size: 13px; color: var(--muted); margin-top: 3px; }
</style>
</head>
<body>
  <section class="card card--back" aria-label="Card back">
    <div class="social">
      <span class="social__item"><span class="social__mark"></span>Glimmer</span>
      <span class="social__item"><span class="social__mark"></span>Chirply</span>
    </div>
  </section>

  <section class="card card--front" aria-label="Card front">
    <div class="brand">
      <div class="brand__name">Velvet Lantern<span class="brand__dot"></span></div>
      <div class="brand__rule"></div>
      <div class="brand__sub">Weddings and Events</div>
      <div class="brand__tagline">Making every celebration glow with wonder...</div>
    </div>

    <div class="contact">
      <div class="contact__row">
        <svg class="contact__icon" viewBox="0 0 34 34" aria-hidden="true">
          <circle cx="17" cy="10" r="7" fill="var(--ink)"/>
          <path d="M4 32c0-8 6-13 13-13s13 5 13 13z" fill="var(--ink)"/>
        </svg>
        <span class="contact__bar"></span>
        <div class="contact__text">
          <div class="person__name">Rosalind Merrow</div>
          <div class="person__role">Event Manager / Owner</div>
        </div>
      </div>

      <div class="contact__row">
        <svg class="contact__icon" viewBox="0 0 34 34" aria-hidden="true">
          <path d="M17 2a11 11 0 0 0-11 11c0 8 11 19 11 19s11-11 11-19A11 11 0 0 0 17 2z" fill="var(--ink)"/>
          <circle cx="17" cy="13" r="4.5" fill="var(--card)"/>
        </svg>
        <span class="contact__bar"></span>
        <div class="contact__text">14 Wattle Arcade Level 2<br>Carlton VIC</div>
      </div>

      <div class="contact__row">
        <svg class="contact__icon" viewBox="0 0 34 34" aria-hidden="true">
          <circle cx="17" cy="17" r="14" fill="none" stroke="var(--ink)" stroke-width="3"/>
          <ellipse cx="17" cy="17" rx="6" ry="14" fill="none" stroke="var(--ink)" stroke-width="2.5"/>
          <line x1="3" y1="17" x2="31" y2="17" stroke="var(--ink)" stroke-width="2.5"/>
          <line x1="6" y1="10" x2="28" y2="10" stroke="var(--ink)" stroke-width="2"/>
          <line x1="6" y1="24" x2="28" y2="24" stroke="var(--ink)" stroke-width="2"/>
        </svg>
        <span class="contact__bar contact__bar--tall"></span>
        <div class="contact__text">0491 868 254<br>rosalind@velvetlanternco.com.au<br>www.velvetlanternco.com.au</div>
      </div>
    </div>
  </section>
</body>
</html>
```